Local massage therapist needs some new marketing material

Hi there! I am a massage therapist here in Denver, CO in Alder Bend(shopping and art district) of the city. My business is called Lumo Bodywork of Denver. My practice has an eastern influence and I do reflexology, thai massage and use Chinese herbs, etc. I know all my clients and pay close attention to details. I am also very respectful of tradition and it shows in how I work. I tend to like modern, clean, fun, Asian designs. I am wanting a new business card and brochure. I have a logo and branding for my business that I want used in the design. Currently, the sign for my building is purple and I think my logo was designed to be purple. I will attach pictures of it and can send whatever files are necessary so it can be integrated into the brochure, etc. I like the purple but open to using other colors as well. Thanks!
My website is lumobodyworkofdenver.example where info can be gathered about me and services/fees for brochure.
Updates

Just increased budget. Please see new feedback in discussion thread.

Thanks!

                                       HEY ALL,

Just wanted to let you know that I made a change to my website. It is on the Prices Page. I no longer have the frequent  flyer prices but I added discounts. Let me know if you have any questions. Thanks so much!

Target Market(s)

healthy, urban, educated, upper middle class, yogis

Industry/Entity Type

Marketing

Requirements
Must have
• logo stays purple
Should not have
• not too busy

```html
<!DOCTYPE html>
<html lang="en">
<head>
<meta charset="utf-8">
<title>Lumo Bodywork of Denver – Brochure</title>
<link rel="stylesheet" href="https://fonts.googleapis.com/css2?family=Bitter:wght@400;500&family=Open+Sans:wght@300;400&display=swap">
<style>
  :root {
    --purple-deep: #5a2a8c;
    --purple-mid: #7a34a6;
    --ink: #2d2a33;
    --white: #ffffff;
    --portrait-cool: #9fd6d8;
    --portrait-warm: #e8b6b4;
  }
  html, body {
    margin: 0;
    padding: 0;
    width: 1200px;
    height: 944px;
    overflow: hidden;
    background: #f2f0f4;
  }
  .brochure {
    position: relative;
    width: 1200px;
    height: 944px;
    background: var(--white);
    overflow: hidden;
    font-family: "Open Sans", sans-serif;
    color: var(--ink);
  }
  .backdrop { position: absolute; inset: 0; }

  /* Left panel */
  .benefits-title {
    position: absolute; left: 30px; top: 30px; margin: 0;
    font-family: "Bitter", serif; font-weight: 500; font-size: 31px; line-height: 40px;
    letter-spacing: 1.5px; color: var(--purple-deep);
  }
  .benefits-list {
    position: absolute; left: 30px; top: 85px; width: 300px;
    margin: 0; padding: 0; list-style: none;
    font-size: 16px; line-height: 22px; color: var(--ink);
  }
  .benefits-list li {
    position: relative; padding-left: 18px; margin-bottom: 6px;
  }
  .benefits-list li::before {
    content: "+"; position: absolute; left: 0; top: -1px;
    color: var(--purple-mid); font-size: 17px;
  }
  .portrait {
    position: absolute; left: 0; top: 580px; width: 272px; height: 184px;
    background: linear-gradient(135deg, var(--portrait-cool), #f4e9ea 50%, var(--portrait-warm));
  }
  .brand-name {
    position: absolute; font-family: "Open Sans", sans-serif; font-weight: 300;
    color: var(--purple-deep); letter-spacing: 6px; margin: 0; white-space: nowrap;
  }
  .brand-name.footer { left: 33px; top: 808px; font-size: 46px; line-height: 1; }
  .address {
    position: absolute; left: 226px; top: 816px; font-size: 15px; line-height: 22px;
  }
  .address svg { position: absolute; left: -13px; top: 4px; }
  .contact {
    position: absolute; left: 33px; font-size: 15px; display: flex; align-items: center; gap: 10px;
  }
  .contact.email { top: 872px; }
  .contact.web { top: 899px; }

  /* Middle panel */
  .ornament {
    position: absolute; border-radius: 50%;
    background: radial-gradient(circle, rgba(255,255,255,0.35), rgba(255,255,255,0.08) 70%);
  }
  .ornament.middle { left: 550px; top: 35px; width: 100px; height: 100px; }
  .ornament.right { left: 846px; top: 30px; width: 110px; height: 110px; }
  .tagline {
    position: absolute; left: 420px; width: 360px; top: 157px; margin: 0;
    text-align: center; font-family: "Bitter", serif; font-size: 26px;
    line-height: 39px; color: var(--white);
  }
  .tagline-box {
    position: absolute; left: 443px; top: 240px; width: 314px; height: 48px;
    background: var(--white); color: var(--purple-deep);
    font-family: "Bitter", serif; font-size: 27px; line-height: 48px; text-align: center;
  }
  .service-title {
    position: absolute; left: 400px; width: 270px; top: 321px; margin: 0;
    text-align: center; font-weight: 300; font-size: 40px; line-height: 52px;
    color: var(--white);
  }
  .phone-box {
    position: absolute; left: 404px; top: 805px; width: 234px; height: 42px;
    background: var(--white); color: var(--purple-deep);
    display: flex; align-items: center; gap: 26px; padding-left: 14px; box-sizing: border-box;
    font-size: 23px;
  }

  /* Right panel */
  .brand-name.cover { left: 970px; top: 58px; font-size: 52px; line-height: 1; color: var(--white); }
  .cover-headline {
    position: absolute; left: 830px; width: 314px; top: 722px; margin: 0;
    text-align: center; font-family: "Bitter", serif; font-weight: 500;
    font-size: 32px; line-height: 49px; letter-spacing: 2px; color: var(--white);
  }
  .cover-rule {
    position: absolute; left: 844px; top: 876px; width: 290px; height: 1px; background: var(--white);
  }
  .cover-url {
    position: absolute; left: 810px; width: 356px; top: 895px; text-align: center;
    font-family: "Bitter", serif; font-size: 19px; color: var(--white); white-space: nowrap;
  }
</style>
</head>
<body>
<main class="brochure">
  <svg class="backdrop" width="1200" height="944" viewBox="0 0 1200 944" aria-hidden="true">
    <defs>
      <linearGradient id="purpleField" x1="0" y1="0" x2="1" y2="1">
        <stop offset="0" stop-color="#6a2f9c"/>
        <stop offset="0.5" stop-color="#8a3cb4"/>
        <stop offset="1" stop-color="#5a2a8c"/>
      </linearGradient>
      <radialGradient id="massageScene" cx="0.55" cy="0.55" r="0.7">
        <stop offset="0" stop-color="#a8683e"/>
        <stop offset="0.6" stop-color="#6e4226"/>
        <stop offset="1" stop-color="#2e1c12"/>
      </radialGradient>
      <clipPath id="sceneClip"><circle cx="1250" cy="780" r="615"/></clipPath>
    </defs>
    <path d="M444,0 L1200,0 L1200,944 L420,944 C300,720 280,330 444,0 Z" fill="url(#purpleField)"/>
    <path d="M330,250 C305,520 345,770 470,944" fill="none" stroke="#ffffff" stroke-width="2"/>
    <line x1="401" y1="0" x2="401" y2="944" stroke="#ffffff" stroke-opacity="0.12"/>
    <line x1="799" y1="0" x2="799" y2="944" stroke="#000000" stroke-opacity="0.08"/>
    <circle cx="1250" cy="780" r="640" fill="none" stroke="#ffffff" stroke-width="2.5"/>
    <g clip-path="url(#sceneClip)" role="img" aria-label="Photo of a therapist's hands massaging a client's back beside a spa tray">
      <rect x="600" y="100" width="600" height="844" fill="url(#massageScene)"/>
    </g>
  </svg>

  <!-- Left panel -->
  <h2 class="benefits-title">BENEFITS</h2>
  <ul class="benefits-list">
    <li>Relaxing the whole body</li>
    <li>Loosening and relieving tired, aching and tight muscles</li>
    <li>Increasing flexibility and range of motion</li>
    <li>Diminishing chronic pain</li>
    <li>Calming the nervous system</li>
    <li>Lowering blood pressure and heart rate</li>
    <li>Enhancing skin tone Aiding in recovery following injuries and illness</li>
    <li>Strengthening the immune system</li>
    <li>Reducing headaches and mental stress</li>
    <li>Improving relaxation</li>
    <li>Promoting restful sleep</li>
  </ul>
  <div class="portrait" role="img" aria-label="Portrait photo of the massage therapist"></div>

  <p class="brand-name footer">LUMO</p>
  <div class="address">
    <svg width="10" height="14" viewBox="0 0 10 14" aria-hidden="true"><path d="M5 0C2.2 0 0 2.2 0 5c0 3.6 5 9 5 9s5-5.4 5-9c0-2.8-2.2-5-5-5zm0 7a2 2 0 110-4 2 2 0 010 4z" fill="#5a2a8c"/></svg>
    1450 E 4th Ave,<br>Denver, CO 80206
  </div>
  <div class="contact email">
    <svg width="22" height="15" viewBox="0 0 22 15" aria-hidden="true"><rect x="0" y="0" width="22" height="15" fill="#5a2a8c"/><path d="M1 1l10 8 10-8" fill="none" stroke="#fff" stroke-width="1.6"/></svg>
    info@lumobodyworkofdenver.example
  </div>
  <div class="contact web">
    <svg width="20" height="20" viewBox="0 0 20 20" aria-hidden="true"><circle cx="10" cy="10" r="9" fill="#5a2a8c"/><g fill="none" stroke="#fff" stroke-width="1.1"><ellipse cx="10" cy="10" rx="4" ry="9"/><line x1="1" y1="10" x2="19" y2="10"/><path d="M3 5h14M3 15h14"/></g></svg>
    www.lumobodyworkofdenver.example
  </div>

  <!-- Middle panel -->
  <div class="ornament middle" role="img" aria-label="Lotus ornament"></div>
  <p class="tagline">May You Awaken<br>to The Light of</p>
  <div class="tagline-box">Your Own True Nature</div>
  <h1 class="service-title">BODYWORK<br>OF<br>DENVER</h1>
  <div class="phone-box">
    <svg width="16" height="24" viewBox="0 0 16 24" aria-hidden="true"><path d="M4 1c-2 1-3 3-3 6 0 6 4 13 8 16 2 1 4 1 6-1l-3-5-3 1c-2-2-4-7-4-10l3-1-1-6z" fill="#5a2a8c"/></svg>
    303.555.0142
  </div>

  <!-- Right panel -->
  <div class="ornament right" role="img" aria-label="Lotus ornament"></div>
  <p class="brand-name cover">LUMO</p>
  <h2 class="cover-headline">YOUR PATH<br>TO WELLNESS<br>BEGINS HERE!</h2>
  <div class="cover-rule"></div>
  <div class="cover-url">www.lumobodyworkofdenver.example</div>
</main>
</body>
</html>
```